Profesional personal website needs design and business card

I need a business card with my professional name as a logo "Dorian Vitality" for my business. I am a Wellness Coach, consultant and trainer. So it should be professional, wellness oriented and modern.

Target Market(s)

Private clients, governments, corporations. Luxury and high market.

Industry/Entity Type

Health And Wellness

Contact Information for Business Card

Dorian Vitality should be the logo

Colors

Designer to choose colors to be used in the design.

Requirements
Must have
• Dorian Vitality
• Name: Tomás Lirandel
• Wellness Coach, Consultant & Trainer.
• Website: www.dorianvitality-example.com
• Phone:
• Spain (+34) 612 480 317
• (USA) +1 (555) 610 4829
Nice to have
• The most important is the design of "Dorian Vitality", as this is going to be my personal brand logo. It should be professional, wellness, high end and actual.
Should not have
• no golds, no baroque style..

```html
<!DOCTYPE html>
<html lang="en">
<head>
<meta charset="utf-8">
<title>Dorian Vitality — Tomás Lirandel Business Card</title>
<link rel="stylesheet" href="https://fonts.googleapis.com/css2?family=Quicksand:wght@300;400&display=swap">
<style>
  :root {
    --frame: #333333;
    --card: #ffffff;
    --mint: #4ff5b2;
    --mint-soft: #d2faec;
    --ink: #333333;
  }
  * { margin: 0; padding: 0; box-sizing: border-box; }
  html, body {
    width: 1200px;
    height: 686px;
    overflow: hidden;
    background: var(--frame);
    font-family: "Quicksand", sans-serif;
  }
  .card {
    position: absolute;
    left: 43px;
    top: 43px;
    width: 1114px;
    height: 599px;
    background: var(--card);
  }
  .brand-mark {
    position: absolute;
    left: 0;
    width: 100%;
    top: 22px;
    text-align: center;
    font-weight: 400;
    font-size: 22px;
    line-height: 1;
    letter-spacing: 8px;
    color: var(--mint);
    text-transform: uppercase;
  }
  .person-name {
    position: absolute;
    left: 0;
    width: 100%;
    top: 58px;
    text-align: center;
    font-weight: 300;
    font-size: 98px;
    line-height: 1;
    letter-spacing: 7px;
    color: var(--mint);
    text-transform: uppercase;
  }
  .role-dots {
    position: absolute;
    left: 0;
    top: 0;
  }
  .role {
    position: absolute;
    width: 380px;
    text-align: center;
    font-weight: 400;
    font-size: 46px;
    line-height: 57px;
    letter-spacing: 4px;
    color: var(--ink);
    text-transform: uppercase;
  }
  .role--coach { left: 1px; top: 242px; }
  .role--consultant { left: 367px; top: 270px; }
  .role--trainer { left: 732px; top: 270px; }
  .contact {
    position: absolute;
    left: 0;
    width: 100%;
    top: 416px;
    text-align: center;
    font-weight: 400;
    font-size: 36px;
    line-height: 48px;
    letter-spacing: 2px;
    color: var(--ink);
  }
  .contact .web { text-transform: uppercase; }
</style>
</head>
<body>
  <div class="card">
    <p class="brand-mark">Dorian Vitality</p>
    <h1 class="person-name">Tomás Lirandel</h1>

    <svg class="role-dots" width="1114" height="599" viewBox="0 0 1114 599" aria-hidden="true">
      <circle cx="191" cy="298" r="77" fill="var(--mint-soft)"/>
      <circle cx="557" cy="298" r="77" fill="var(--mint-soft)"/>
      <circle cx="920" cy="298" r="77" fill="var(--mint-soft)"/>
    </svg>

    <p class="role role--coach">Wellness<br>Coach</p>
    <p class="role role--consultant">Consultant</p>
    <p class="role role--trainer">Trainer</p>

    <div class="contact">
      <p class="web">www.dorianvitality-example.com</p>
      <p class="phone">(+34) 612 480 317</p>
      <p class="phone">+1 (555) 610 4829</p>
    </div>
  </div>
</body>
</html>
```